Company Website for Varnoth Signal, an open source data analytics company focused on relationship and li

I need a company/brand website for our new startup, Varnoth Signal LLC. We are a company focused on using life pattern analysis techniques, looking at relationships and how relationships, attributes, and activity cluster to infer aggregate information about individuals and groups. Our focus is on improving the digital advertising market.

We have a company logo which I will upload shortly.

Target Market(s)

Digital Advertising

Number of Pages Required

3 page

Font styles to use
Sans Serif

Requirements
Must have
• An main page, about us, contact page.
Nice to have
• Varnoth Signal relies on state of the art analytics applied to a the digital marketing space. While it is heavy in science, we also understand the art of influence. The website should have a scientific edge but also a flair that illustrates our focus on applying the hard science and analytics to influencing the behavior of people.

```html
<!DOCTYPE html>
<html lang="en">
<head>
<meta charset="utf-8">
<title>Varnoth Signal — Improving the Digital Advertising Market</title>
<link href="https://fonts.googleapis.com/css2?family=Montserrat:wght@600;700;800&family=Lato:wght@400;700&display=swap" rel="stylesheet">
<style>
:root{
  --orange:#f7931e;
  --orange-soft:#fbd9ad;
  --peach:#fde6cc;
  --blue:#1f73be;
  --blue-soft:#d6e6f7;
  --ink:#111111;
  --text:#555555;
  --muted:#777777;
  --white:#ffffff;
}
*{box-sizing:border-box;margin:0;padding:0}
html,body{width:1200px;height:2961px;overflow:hidden;background:var(--white)}
body{position:relative;font-family:'Lato',sans-serif;color:var(--text)}
.abs{position:absolute}
.backdrop{position:absolute;left:0;top:0;width:1200px;height:2961px;z-index:0}
.layer{position:relative;z-index:1}

.brand{left:79px;top:48px;display:flex;align-items:center;gap:12px}
.brand-mark{width:22px;height:22px;background:var(--orange)}
.brand-name{font-family:'Montserrat',sans-serif;font-weight:700;font-size:26px;color:var(--blue);letter-spacing:.5px}

.nav{top:38px;left:687px;display:flex;align-items:center;font-size:15px;color:var(--white)}
.nav a{color:var(--white);text-decoration:none;margin-right:26px;position:relative}
.nav a.active::before{content:"";position:absolute;left:-6px;right:-6px;top:-16px;height:2px;background:var(--white)}
.nav .join{border:1.5px solid var(--white);border-radius:22px;width:146px;height:42px;display:flex;align-items:center;justify-content:center;margin:0 0 0 16px}

.hero-title{left:79px;top:222px;font-family:'Montserrat',sans-serif;font-weight:800;font-size:35px;line-height:46px;color:var(--ink);letter-spacing:.5px}
.btn{display:flex;align-items:center;justify-content:center;border-radius:26px;background:var(--blue);color:var(--white);font-family:'Montserrat',sans-serif;font-weight:700;letter-spacing:.5px;box-shadow:0 10px 20px rgba(31,115,190,.3)}
.hero-btn{left:79px;top:387px;width:195px;height:51px;font-size:18px}
.hero-art{left:543px;top:245px;width:622px;height:300px;border-radius:16px;background:linear-gradient(135deg,#f2f4fb,#dfe6f6 60%,#fbd9ad)}

.section-title{left:0;width:1200px;text-align:center;font-family:'Montserrat',sans-serif;font-weight:800;font-size:40px;color:var(--ink);letter-spacing:.5px}
.rule{left:568px;width:64px;height:3px;background:var(--blue)}
.lead{left:265px;width:670px;text-align:center;font-size:13px;line-height:25px;color:var(--text)}

.focus-item{width:300px}
.focus-item h3{font-family:'Lato',sans-serif;font-weight:400;font-size:21px;color:#333;margin-bottom:8px}
.focus-item p{font-size:13px;line-height:25px;color:var(--text)}
.focus-left{text-align:right}
.card{background:var(--white);border-radius:8px;box-shadow:0 8px 24px rgba(0,0,0,.08)}
.icon-card{width:93px;height:93px;display:flex;align-items:center;justify-content:center}
.shadow-card{width:72px;height:72px;background:#fafafa}
.focus-hub{left:509px;top:928px;width:178px;height:177px;display:flex;align-items:center;justify-content:center;text-align:center;font-family:'Montserrat',sans-serif;font-weight:700;font-size:22px;line-height:26px;color:var(--blue)}

.about-art{left:77px;top:1362px;width:417px;height:399px;border-radius:14px;background:linear-gradient(160deg,#2a7bc6,#1f6db5)}
.sq{background:var(--blue);border-radius:5px;box-shadow:0 8px 16px rgba(31,115,190,.3)}
.about-title{left:655px;top:1388px;font-family:'Montserrat',sans-serif;font-weight:800;font-size:40px;color:var(--ink)}
.about-copy{left:655px;top:1484px;width:440px;font-size:13px;line-height:25px}
.about-copy p+p{margin-top:10px}
.about-btn{left:657px;top:1670px;width:200px;height:51px;font-size:18px}

.post-img{width:272px;height:197px;border-radius:12px}
.post-img.one{background:linear-gradient(135deg,#cfd8df,#7d8a96 60%,#3e4a57)}
.post-img.two{background:linear-gradient(135deg,#3b4a58,#8a7a6a 55%,#f3c98e)}
.post-card{width:272px;height:198px;padding:30px 24px}
.post-card h4{font-family:'Lato',sans-serif;font-weight:400;font-size:17px;line-height:29px;color:#222}
.post-card .date{font-size:13px;margin:8px 0 6px;color:var(--text)}
.post-card p{font-size:13px;line-height:25px;color:var(--text)}

.newsletter{left:77px;top:2521px;width:1046px;height:270px;border-radius:20px;text-align:center}
.newsletter h2{margin-top:48px;font-family:'Montserrat',sans-serif;font-weight:800;font-size:40px;color:var(--ink)}
.newsletter .sub{margin-top:10px;font-size:13px;color:var(--text)}
.subscribe{position:absolute;left:186px;top:158px;width:675px;height:44px;border:1.5px solid var(--orange);border-radius:22px;display:flex;align-items:center;justify-content:space-between;padding-left:22px}
.subscribe span{font-size:13px;color:#777}
.subscribe .go{height:40px;width:158px;border-radius:20px;background:var(--orange);color:var(--white);font-family:'Montserrat',sans-serif;font-weight:700;font-size:19px;display:flex;align-items:center;justify-content:center;margin-right:1px}

.footer-links{left:0;width:1200px;top:2864px;text-align:center;font-size:13px;color:#444}
.footer-links span{margin:0 12px}
.copyright{left:0;width:1200px;top:2910px;text-align:center;font-size:13px;color:#444}
</style>
</head>
<body>
<svg class="backdrop" viewBox="0 0 1200 2961" aria-hidden="true">
  <path d="M600 0 H1200 V420 C1120 520 960 580 820 570 C660 560 540 470 520 330 C505 200 545 80 600 0Z" fill="var(--peach)"/>
  <path d="M640 0 H1200 V330 C1120 460 990 530 860 530 C700 530 580 440 565 310 C552 190 590 80 640 0Z" fill="var(--orange-soft)"/>
  <path d="M660 0 H1200 V240 C1140 400 1000 490 870 495 C720 500 605 410 595 290 C585 170 615 70 660 0Z" fill="var(--orange)"/>
  <path d="M0 1060 C180 900 380 840 540 880 C640 920 660 1060 640 1220 C610 1460 470 1700 300 1870 C190 1960 80 2000 0 2010Z" fill="var(--blue-soft)"/>
  <path d="M1200 2540 C1100 2420 940 2410 790 2480 C620 2560 560 2760 600 2961 H1200Z" fill="var(--peach)"/>
</svg>

<div class="layer">
  <header>
    <div class="abs brand"><span class="brand-mark"></span><span class="brand-name">Varnoth Signal</span></div>
    <nav class="abs nav">
      <a class="active">HOME</a><a>ABOUT US</a><a>CONTACT</a><span class="join">JOIN NOW</span>
    </nav>
  </header>

  <section class="hero">
    <h1 class="abs hero-title">IMPROVING THE<br>DIGITAL ADVERTISING<br>MARKET</h1>
    <a class="abs btn hero-btn">CONTACT US</a>
    <div class="abs hero-art" role="img" aria-label="Illustration of a team working with analytics dashboards and SEO charts around a large screen"></div>
  </section>

  <section class="focus">
    <h2 class="abs section-title" style="top:676px">COMPANY FOCUS</h2>
    <div class="abs rule" style="top:744px"></div>
    <p class="abs lead" style="top:765px">Lorem Ipsum is simply dummy text of the printing and typesetting industry. Lorem Ipsum has been the industry's standard dummy text ever since the 1500s, when an unknown printer took a galley.</p>

    <div class="abs focus-item focus-left" style="left:57px;top:872px"><h3>Analysis techniques</h3><p>Lorem Ipsum is simply dummy text of the printing and typesetting industry.</p></div>
    <div class="abs focus-item" style="left:847px;top:872px"><h3>Attributes</h3><p>Lorem Ipsum is simply dummy text of the printing and typesetting industry.</p></div>
    <div class="abs focus-item focus-left" style="left:57px;top:1077px"><h3>Relationships</h3><p>Lorem Ipsum is simply dummy text of the printing and typesetting industry.</p></div>
    <div class="abs focus-item" style="left:847px;top:1077px"><h3>Activity cluster</h3><p>Lorem Ipsum is simply dummy text of the printing and typesetting industry.</p></div>

    <div class="abs card shadow-card" style="left:398px;top:908px"></div>
    <div class="abs card shadow-card" style="left:728px;top:908px"></div>
    <div class="abs card shadow-card" style="left:398px;top:1118px"></div>
    <div class="abs card shadow-card" style="left:728px;top:1118px"></div>
    <div class="abs card focus-hub">Varnoth<br>Signal</div>

    <div class="abs card icon-card" style="left:418px;top:869px">
      <svg width="46" height="46" viewBox="0 0 46 46" fill="none" stroke="var(--orange)" stroke-width="2.5"><circle cx="20" cy="20" r="14"/><path d="M30 30 L42 42"/><path d="M10 22 L16 16 L21 24 L26 13 L30 20"/></svg>
    </div>
    <div class="abs card icon-card" style="left:687px;top:869px">
      <svg width="46" height="46" viewBox="0 0 46 46" fill="none" stroke="var(--orange)" stroke-width="2.5"><rect x="4" y="5" width="8" height="8"/><rect x="4" y="19" width="8" height="8"/><rect x="4" y="33" width="8" height="8"/><path d="M17 9 H42 M17 23 H42 M17 37 H42"/><path d="M5 9 L8 12 L13 5"/></svg>
    </div>
    <div class="abs card icon-card" style="left:418px;top:1076px">
      <svg width="50" height="46" viewBox="0 0 50 46" fill="none" stroke="var(--orange)" stroke-width="2.5" stroke-linejoin="round"><path d="M2 16 L12 10 L22 14 L30 10 L48 18"/><path d="M12 10 L4 28 L14 38 L20 34 L26 40 L40 28 L48 18"/><path d="M22 14 L16 22 L22 26 L30 18 L40 28"/></svg>
    </div>
    <div class="abs card icon-card" style="left:687px;top:1076px">
      <svg width="46" height="46" viewBox="0 0 46 46" fill="none" stroke="var(--orange)" stroke-width="2.5"><rect x="3" y="5" width="40" height="36" rx="2"/><path d="M3 13 H43"/><path d="M8 27 H16 L20 19 L25 34 L29 24 L38 24"/></svg>
    </div>
  </section>

  <section class="about">
    <div class="abs about-art" role="img" aria-label="Illustration of a team collaborating around a long table with laptops"></div>
    <div class="abs sq" style="left:415px;top:1316px;width:29px;height:29px"></div>
    <div class="abs sq" style="left:491px;top:1308px;width:41px;height:41px"></div>
    <div class="abs sq" style="left:403px;top:1377px;width:82px;height:78px"></div>
    <div class="abs sq" style="left:527px;top:1399px;width:52px;height:52px"></div>
    <div class="abs sq" style="left:548px;top:1713px;width:52px;height:50px"></div>
    <h2 class="abs about-title">ABOUT US</h2>
    <div class="abs rule" style="left:655px;top:1454px"></div>
    <div class="abs about-copy">
      <p>Lorem Ipsum is simply dummy text of the printing and typesetting industry. Lorem Ipsum has been the industry's standard dummy text ever since the 1500s, when an unknown printer took a galley of type and scrambled it to make a type specimen book.</p>
      <p>Lorem Ipsum is simply dummy text of the printing and typesetting industry. Lorem Ipsum has been the industry's standard dummy.</p>
    </div>
    <a class="abs btn about-btn">KNOW MORE</a>
  </section>

  <section class="blog">
    <h2 class="abs section-title" style="top:1893px">BLOG POST</h2>
    <div class="abs rule" style="top:1960px"></div>
    <p class="abs lead" style="top:1980px">Lorem Ipsum is simply dummy text of the printing and typesetting industry. Lorem Ipsum has been the industry's standard dummy text ever since the 1500s, when an unknown printer took a galley.</p>

    <div class="abs post-img one" style="left:77px;top:2073px" role="img" aria-label="Photo of hands working on a laptop at a desk"></div>
    <article class="abs card post-card" style="left:306px;top:2177px">
      <h4>Lorem Ipsum is simply dummy text of the.</h4>
      <div class="date">21 SEP 2018</div>
      <p>Lorem Ipsum is simply dummy text of the printing and typeset.</p>
    </article>

    <div class="abs post-img two" style="left:622px;top:2073px" role="img" aria-label="Photo of colleagues reviewing work together"></div>
    <article class="abs card post-card" style="left:851px;top:2177px">
      <h4>Lorem Ipsum is simply dummy text of the.</h4>
      <div class="date">21 SEP 2018</div>
      <p>Lorem Ipsum is simply dummy text of the printing and typeset.</p>
    </article>
  </section>

  <section class="abs card newsletter">
    <h2>NEWSLETTER</h2>
    <p class="sub">Subscribe to our newsletter to get more info and lates update</p>
    <div class="subscribe"><span>Enter your email</span><span class="go">SUBSCRIBE</span></div>
  </section>

  <footer>
    <div class="abs footer-links">About us<span>|</span>Contact us<span>|</span>Privacy Policy</div>
    <div class="abs copyright">©Varnoth Signal - 2018. All Rights Reserved.</div>
  </footer>
</div>
</body>
</html>
```